A business card design for a dental office. We have Two doctors working here. We practice general de

I already have a logo designed for the office with the name and a slogan.
Now I need to create design for a business card using the same logo.
Details Needed on the front side of the card are :
Bernard K. Oswin, DDS
Gerald M Fenwick, DDS
418 Birch Lane
Millbrook, ST 00000
Phone : 555 019 4831
Fax : 555 019 4832
Website : WWW.BrightmoorToothHaven.Com
Office hours by appointment
On the back side of the card need :
Appointment
Date....................Time...................
With....................................
If unable to keep your appointment, please give 24-48 hours notice in order to avoid broken appointment fee.

Industry/Entity Type

Dental Clinic

Contact Information for Business Card

Bernard K. Oswin, DDS
Gerald M Fenwick, DDS
418 Birch Lane
Millbrook, ST 00000
Phone : 555 019 4831
Fax : 555 019 4832
Appointment

Requirements
Must have
• Keep the Name and slogan on the logo on the front of the card. You can move them around the Logo and Name/Slogan of business (Oswin Family Dentistry/Every visit, a brighter smile) as you wish to get a feel of the design.
• Bernard K. Oswin, DDS
• Gerald M Fenwick, DDS
• 418 Birch Lane
• Millbrook, ST 00000
• Phone : 555 019 4831
• Fax : 555 019 4832
• WWW.BrightmoorToothHaven.Com
• Keep these three groups above as they are together now in different areas of the front side.
• On the back side of the card need :
• Appointment
• Date....................Time...................
• With....................................
• If unable to keep your appointment, please give 24-48 hours notice in order to avoid broken appointment fee.

```html
<!DOCTYPE html>
<html lang="en">
<head>
<meta charset="utf-8">
<title>Oswin Family Dentistry – Business Card</title>
<link rel="stylesheet" href="https://fonts.googleapis.com/css2?family=Source+Sans+3:wght@400;600;700&display=swap">
<style>
  :root{
    --bg:#ecebea;
    --blue-light:#9cc8ec;
    --blue-mid:#3f86c9;
    --blue-deep:#1659a6;
    --red:#e8232f;
    --teal:#1a9f7e;
    --navy:#1f5a9e;
    --white:#ffffff;
    --faint:#f1f1f1;
    --mark-front:rgba(255,255,255,.25);
    --mark-back:#d9ebf6;
  }
  *{box-sizing:border-box;margin:0;padding:0}
  html,body{width:1200px;height:900px;overflow:hidden}
  body{background:var(--bg);font-family:"Source Sans 3",sans-serif;position:relative}

  .card{position:absolute;width:556px;height:344px;overflow:hidden;box-shadow:0 4px 14px rgba(0,0,0,.18)}

  /* Front */
  .card-front{left:238px;top:61px;
    background:linear-gradient(180deg,var(--blue-light) 0%,var(--blue-mid) 45%,var(--blue-deep) 80%,var(--blue-deep) 100%);color:var(--white)}
  .front-mark{position:absolute;left:60px;top:80px;width:200px;display:flex;flex-direction:column;align-items:center;gap:10px}
  .front-mark .dot{width:110px;height:110px;border-radius:50%;background:var(--mark-front)}
  .front-mark .name{font-weight:700;font-size:17px;color:var(--white);text-align:center}
  .doctors{position:absolute;left:293px;top:87px;font-weight:600;font-size:17.5px;line-height:27px}
  .contacts{position:absolute;left:293px;top:153px;list-style:none;font-size:15.5px;line-height:20px}
  .contacts li{display:flex;align-items:center;gap:8px}
  .contacts svg{width:12px;height:12px;fill:var(--white)}
  .address{position:absolute;left:0;right:0;top:262px;text-align:center;font-size:16px}
  .hours-band{position:absolute;left:0;right:0;top:292px;height:36px;background:var(--red);
    display:flex;align-items:center;justify-content:center;font-size:16px}

  /* Back */
  .card-back{left:458px;top:518px;background:var(--white)}
  .back-deco{position:absolute;left:300px;top:40px;width:420px;height:420px;border-radius:50%;background:var(--faint)}
  .brand{position:absolute;left:62px;top:30px;display:flex;align-items:center;gap:12px}
  .brand .dot{width:110px;height:110px;border-radius:50%;background:var(--mark-back)}
  .brand .name{font-weight:600;font-size:22px;letter-spacing:1.8px;color:var(--navy);text-transform:uppercase}
  .slogan{position:absolute;left:212px;top:99px;display:flex;align-items:center;gap:7px;
    color:var(--red);font-size:10px;letter-spacing:2px;text-transform:uppercase}
  .slogan::before,.slogan::after{content:"";width:26px;height:1px;background:var(--red)}
  .appt-title{position:absolute;left:0;right:0;top:145px;text-align:center;
    color:var(--red);font-weight:600;font-size:22px}
  .field{position:absolute;display:flex;align-items:flex-end;gap:10px;color:var(--red);font-weight:600;font-size:17px}
  .field .line{border-bottom:2px dotted var(--teal);height:14px;margin-bottom:4px}
  .f-date{left:82px;top:190px}
  .f-time{left:272px;top:190px}
  .f-with{left:82px;top:242px}
  .notice{position:absolute;left:0;right:0;top:282px;text-align:center;font-weight:600;font-size:16.5px;line-height:21px}
  .notice .r{color:var(--red)}
  .notice .t{color:var(--teal);display:block}
</style>
</head>
<body>

<section class="card card-front">
  <div class="front-mark">
    <span class="dot"></span>
    <span class="name">Oswin Family Dentistry</span>
  </div>
  <div class="doctors">
    <p>Bernard K. Oswin, DDS</p>
    <p>Gerald M Fenwick, DDS</p>
  </div>
  <ul class="contacts">
    <li><svg viewBox="0 0 12 12"><path d="M2.5 0.5l2 2.5-1.2 1.3c.7 1.6 2 2.9 3.5 3.6l1.3-1.2 2.4 2-1.3 2.3C4.8 10.8 1.2 7.2 0.3 1.9z"/></svg>555 019 4831</li>
    <li><svg viewBox="0 0 12 12"><path d="M1 4h10v7H1zM3 0.5h6V4H3zM3 6h2v1.5H3zm4 0h2v1.5H7zM3 8.5h2V10H3zm4 0h2V10H7z"/></svg>555 019 4832</li>
    <li><svg viewBox="0 0 12 12"><circle cx="6" cy="6" r="5.5"/></svg>WWW.BrightmoorToothHaven.Com</li>
  </ul>
  <p class="address">418 Birch Lane Millbrook, ST 00000</p>
  <div class="hours-band">Office hours by appointment</div>
</section>

<section class="card card-back">
  <span class="back-deco"></span>
  <div class="brand">
    <span class="dot"></span>
    <span class="name">Oswin Family Dentistry</span>
  </div>
  <p class="slogan">Every visit, a brighter smile</p>
  <h2 class="appt-title">Appointment</h2>
  <div class="field f-date"><span>Date</span><span class="line" style="width:122px"></span></div>
  <div class="field f-time"><span>Time</span><span class="line" style="width:146px"></span></div>
  <div class="field f-with"><span>With</span><span class="line" style="width:336px"></span></div>
  <p class="notice"><span class="r">If unable to keep your appointment, please give 24-48 hours</span><span class="t">notice in order to avoid broken appointment fee.</span></p>
</section>

</body>
</html>
```